kolvarin.link kolvarin.space kolvarin.press website

The website is named KOLVARIN and it will have 3 domain names. kolvarin.link, press, space.
I'd like it to be viewed on Pads, pcs and phones.

page menu:

kolvarin.link(start page): presentation of company. (creative, design, app, new product innovation.)
Here we'll need sosial media icons: plimber, vendoloop, mirtavel, trelvanet. (light but some 'fruity' colors)

kolvarin.press: blog. It will be a 75% picture blog > rest will be text. I need to be able to resize pictures and shape columns to picture size. (light but some 'fruity' colors)

kolvarin.space : the fun part of this web design, however, on entering the page I'd like a non-disclosure agreement where viewer simply click "yes, I agree" after filling out contact info. (check attached document)
We will have space here for uploading PDF files viewers can download. There is also a blog space here to tell in brief about the PDF file. (maybe a space/sci-fi theme her e.g spacechimp, Laika the space dog?)

I will attach the logo here I want you to use > and develop for the .space .press webpage. The logo i uploaded is for the .link page.

Target Market(s)

venture capitalists

Number of Pages Required

3 page

Requirements
Must have
• a few 'fruity colors' but mostly white and grey

```html
<!DOCTYPE html>
<html lang="en">
<head>
<meta charset="utf-8">
<title>Kolvarin Link</title>
<link href="https://fonts.googleapis.com/css2?family=Lato:ital,wght@0,400;0,700;0,900;1,400&family=Open+Sans:wght@400&display=swap" rel="stylesheet">
<style>
  :root {
    --orange: #f07022;
    --orange-dark: #d9571a;
    --amber: #f7a21b;
    --green: #7aa63a;
    --ink: #111111;
    --text: #222222;
    --grey-band: #f1f1f1;
    --caption-bg: #cfcfcf;
    --footer: #2b2b2b;
    --footer-text: #9a9a9a;
    --white: #ffffff;
  }
  * { margin: 0; padding: 0; box-sizing: border-box; }
  html, body { width: 940px; height: 1200px; overflow: hidden; }
  body { position: relative; font-family: "Lato", sans-serif; color: var(--text); background: var(--white); }

  .site-header { position: absolute; left: 0; top: 0; width: 940px; height: 82px; background: linear-gradient(#ffffff, #f3f3f3); }
  .brand { position: absolute; left: 40px; top: 26px; display: flex; align-items: center; gap: 8px; font-weight: 900; font-size: 22px; color: var(--ink); letter-spacing: 0.5px; }
  .brand-mark { width: 18px; height: 18px; background: var(--orange); }
  .contact { position: absolute; top: 26px; display: flex; align-items: center; gap: 9px; font-weight: 700; font-size: 15px; color: var(--ink); white-space: nowrap; }
  .contact-email { left: 498px; }
  .contact-phone { left: 696px; }
  .contact-icon { width: 29px; height: 29px; border-radius: 50%; background: var(--amber); display: flex; align-items: center; justify-content: center; flex: none; }
  .menu-toggle { position: absolute; left: 871px; top: 27px; width: 29px; height: 26px; border: 1.5px solid var(--amber); display: flex; flex-direction: column; justify-content: center; gap: 3px; padding: 0 5px; }
  .menu-toggle span { display: block; height: 1.5px; background: var(--amber); }

  .hero { position: absolute; left: 0; top: 82px; width: 940px; height: 330px; background: linear-gradient(90deg, #3a6aa8 0%, #4a7fbe 45%, #3d70b0 100%); }
  .hero-photo { position: absolute; left: 60px; top: 0; width: 430px; height: 330px; background: radial-gradient(ellipse at 55% 55%, #8fcff0 0%, #3f86c4 45%, rgba(40,60,90,0.6) 100%); }
  .hero-title { position: absolute; left: 514px; top: 96px; width: 400px; font-weight: 700; font-size: 22px; line-height: 33px; color: var(--white); text-transform: uppercase; letter-spacing: 0.4px; }
  .hero-cta { position: absolute; left: 514px; top: 177px; width: 138px; height: 33px; background: var(--amber); border: 1px solid #fff3; color: var(--ink); font-weight: 700; font-size: 17px; text-align: center; line-height: 31px; }
  .hero-dots { position: absolute; left: 514px; top: 227px; display: flex; gap: 5px; }
  .hero-dots span { width: 7px; height: 7px; border-radius: 50%; background: #c9d4e3; }
  .hero-dots span.active { background: var(--ink); }

  .section-title { position: absolute; left: 0; width: 940px; text-align: center; font-weight: 900; font-size: 26px; letter-spacing: 0.3px; }
  .title-rule { position: absolute; height: 1px; }
  .title-rule i { position: absolute; top: -0.5px; height: 2px; background: var(--green); }

  .about-title { top: 438px; color: var(--ink); }
  .about-title em { font-style: normal; color: var(--orange); }
  .about-rule { left: 279px; top: 478px; width: 382px; background: #cccccc; }
  .about-rule i { left: 136px; width: 110px; }
  .about-text { position: absolute; left: 40px; top: 501px; width: 860px; text-align: center; font-size: 12px; line-height: 21.6px; color: var(--text); }

  .services { position: absolute; left: 0; top: 591px; width: 940px; height: 271px; background: var(--grey-band); }
  .service { position: absolute; top: 39px; width: 259px; }
  .service:nth-child(1) { left: 42px; }
  .service:nth-child(2) { left: 341px; }
  .service:nth-child(3) { left: 640px; }
  .service-image { position: relative; height: 157px; border-top: 3px solid var(--orange); }
  .service-image .caption { position: absolute; left: 0; bottom: 0; width: 100%; height: 29px; background: rgba(20,20,20,0.82); color: var(--white); font-weight: 700; font-size: 15px; text-align: center; line-height: 29px; }
  .img-design { background: linear-gradient(160deg, #d9d6d0 0%, #a07a52 55%, #5b3d25 100%); }
  .img-app { background: linear-gradient(160deg, #2f6fc0 0%, #1b4f9a 55%, #0f2c63 100%); }
  .img-idea { background: linear-gradient(160deg, #eef0f2 0%, #d6dadd 50%, #b9bec2 100%); }
  .service-text { height: 36px; background: var(--caption-bg); font-family: "Open Sans", sans-serif; font-size: 11px; line-height: 13px; text-align: center; padding-top: 5px; color: var(--text); }

  .testimonials { position: absolute; left: 0; top: 862px; width: 940px; height: 264px; background: var(--orange); }
  .clients-title { top: 24px; color: var(--white); }
  .clients-title em { font-style: normal; color: var(--ink); }
  .clients-rule { left: 279px; top: 64px; width: 374px; background: #ffffff; }
  .clients-rule i { left: 132px; width: 110px; }
  .quote-card { position: absolute; left: 180px; top: 101px; width: 652px; height: 122px; border: 1px solid #f7b089; border-radius: 10px; }
  .avatar { position: absolute; left: 107px; top: 109px; width: 108px; height: 108px; border-radius: 50%; background: var(--orange-dark); padding: 6px; }
  .avatar div { width: 100%; height: 100%; border-radius: 50%; background: radial-gradient(circle at 50% 45%, #e9e9ec 0%, #b8bcc4 100%); }
  .quote { position: absolute; left: 232px; top: 121px; width: 584px; font-style: italic; font-size: 14px; line-height: 19.6px; letter-spacing: 0.25px; color: var(--white); }
  .quote .mark { font-family: Georgia, serif; font-style: normal; font-weight: 700; font-size: 34px; line-height: 0; color: #f5a47a; vertical-align: -10px; }
  .quote-author { position: absolute; right: 135px; top: 196px; font-weight: 700; font-size: 14px; color: var(--white); }
  .quote-dots { position: absolute; left: 449px; top: 228px; display: flex; gap: 5px; }
  .quote-dots span { width: 7px; height: 7px; border-radius: 50%; background: var(--white); }
  .quote-dots span.active { background: var(--green); }

  .site-footer { position: absolute; left: 0; top: 1126px; width: 940px; height: 74px; background: var(--footer); }
  .social { position: absolute; left: 0; top: 16px; width: 940px; display: flex; justify-content: center; font-size: 11px; font-weight: 700; color: #bdbdbd; }
  .social span { padding: 0 10px; border-left: 1px solid #555; line-height: 14px; }
  .social span:first-child { border-left: none; }
  .copyright { position: absolute; left: 0; top: 48px; width: 940px; text-align: center; font-size: 11px; color: var(--footer-text); }
</style>
</head>
<body>

<header class="site-header">
  <div class="brand"><span class="brand-mark"></span>KOLVARIN</div>
  <div class="contact contact-email">
    <span class="contact-icon">
      <svg width="15" height="11" viewBox="0 0 15 11"><rect x="0.5" y="0.5" width="14" height="10" fill="none" stroke="#fff" stroke-width="1.4"/><path d="M1 1l6.5 5 6.5-5" fill="none" stroke="#fff" stroke-width="1.4"/></svg>
    </span>
    info@kolvarinlink.com
  </div>
  <div class="contact contact-phone">
    <span class="contact-icon">
      <svg width="14" height="14" viewBox="0 0 14 14"><path d="M3 1l2.3 2.8-1.2 1.6c.9 1.8 2.3 3.2 4.1 4.1l1.6-1.2L12.6 10.6 11.2 13C5.8 12.6 1.4 8.2 1 2.8z" fill="#fff"/></svg>
    </span>
    555-218-4093
  </div>
  <div class="menu-toggle"><span></span><span></span><span></span><span></span></div>
</header>

<section class="hero">
  <div class="hero-photo" role="img" aria-label="Businessman holding a tablet, laptop and phone linked by a glowing network around a globe"></div>
  <h1 class="hero-title">Loren ipsum dolor sit amet sie consectetuer adipiscing</h1>
  <div class="hero-cta">GET STARTED</div>
  <div class="hero-dots"><span class="active"></span><span></span><span></span></div>
</section>

<h2 class="section-title about-title"><em>ABOUT</em> KOLVARIN LINK</h2>
<div class="title-rule about-rule"><i></i></div>
<p class="about-text">Lorem ipsum dolor sit amet, consectetuer adipiscing elit, sed diam nonummy nibh euismod tincidunt ut laoreet dolore magna aliquam erat volutpat. Ut wisi enim ad minim veniam, quis nostrud exerci tation ullamcorper suscipit lobortis nisl ut aliquip ex ea commodo consequat. Duis autem vel eum iriure dolor in hendrerit in vulputate velit esse molestie consequat, vel illum dolore eu feugiat nulla facilisis at vero eros et accumsan et iusto o</p>

<section class="services">
  <article class="service">
    <div class="service-image img-design" role="img" aria-label="Laptop showing a website on a wooden desk with notebook and pen">
      <div class="caption">Creative Design</div>
    </div>
    <p class="service-text">Eaque ipsa quae ab illo inventore veritatis<br>et quasi architecto beatae vitae</p>
  </article>
  <article class="service">
    <div class="service-image img-app" role="img" aria-label="Hand holding a smartphone with colourful app icons floating above it">
      <div class="caption">App Development</div>
    </div>
    <p class="service-text">Eaque ipsa quae ab illo inventore veritatis<br>et quasi architecto beatae vitae</p>
  </article>
  <article class="service">
    <div class="service-image img-idea" role="img" aria-label="Hand drawing a yellow light bulb among drafting tools and paper">
      <div class="caption">New Product Innovation</div>
    </div>
    <p class="service-text">Eaque ipsa quae ab illo inventore veritatis<br>et quasi architecto beatae vitae</p>
  </article>
</section>

<section class="testimonials">
  <h2 class="section-title clients-title"><em>WHAT</em> OUR CLIENTS SAY</h2>
  <div class="title-rule clients-rule"><i></i></div>
  <div class="quote-card"></div>
  <div class="avatar"><div role="img" aria-label="Portrait photo of a smiling client"></div></div>
  <p class="quote"><span class="mark">&ldquo;</span> Lorem ipsum dolor sit amet, consectetuer adipiscing elit, sed diam nonummy nibh euismod tincidunt ut laoreet dolore magna aliquam erat volutpat. Ut wisi enim ad minim veniam, quis nostrud exerci tation ullamcorper suscipit. Lorem ipsum dolor sit amet, consectetuer adipiscing elit. diam nonummy nibh euismod tincsetr. <span class="mark">&rdquo;</span></p>
  <p class="quote-author">- Consectetue Radipiscing</p>
  <div class="quote-dots"><span class="active"></span><span></span><span></span><span></span></div>
</section>

<footer class="site-footer">
  <nav class="social"><span>mirtavel</span><span>plimber</span><span>trelvanet</span><span>vendoloop</span></nav>
  <p class="copyright">COPYRIGHT &copy; 2016 KOLVARIN LINK. ALL RIGHT RESERVED</p>
</footer>

</body>
</html>
```